Business Cards Needed for Innovative Healthcare Marketing Company

We are a marketing company focused on healthcare. Our company is all about rebranding yourself renewing your image and generating results. The phoenix stands for "reborn" or "rising" which we provide new brands for our clients we take their old brands and renew it with creativity and innovation. I am looking for a business card with color dimension. I have attached an example of a card I think has the look and feel of what I am trying to accomplish. I like that the card example has black and grey font colors, I like the font placement and the small logo, I really like the use of the colors on the right those are the colors of my logo. My logo is phoenix so maybe incorporating flames similar to that design. I would like the back a solid color maybe red with an opaque version of the logo and website. As a marketing company I am always open to creative liberty!

Target Market(s)

Doctors and business professionals.

Industry/Entity Type

Marketing

Contact Information for Business Card

Valcorne Health Care Marketing
Marla Tenwick- CEO
#(512)638-2974
email-marla@valcorne.com
website- valcorne.com

Font styles to use
Sans Serif

Colors
ec1f27
f37122
ffc214
fbed22
fbf289
f04a50

Requirements
Must have
• The logo and required information
Nice to have
• icons by the information
Should not have
• child like font

```html
<!DOCTYPE html>
<html lang="en">
<head>
<meta charset="utf-8">
<title>Valcorne Health Care Marketing — Business Card</title>
<link href="https://fonts.googleapis.com/css2?family=Open+Sans:wght@300;400;600;700&display=swap" rel="stylesheet">
<style>
  :root {
    --page-bg: #e6e2de;
    --card-bg: #f3f0ed;
    --wine-dark: #6e1519;
    --wine: #8e2227;
    --wine-light: #a8353a;
    --ember: #f37122;
    --flame: #e0562a;
    --brand-text: #8a2a2e;
    --contact-text: #f6e6e2;
  }
  * { margin: 0; padding: 0; box-sizing: border-box; }
  html, body {
    width: 1200px; height: 969px; overflow: hidden;
    background: var(--page-bg);
    font-family: "Open Sans", Arial, sans-serif;
  }
  .canvas { position: relative; width: 1200px; height: 969px; }
  .card {
    position: absolute; left: 100px; top: 200px;
    width: 1000px; height: 568px;
    border-radius: 28px; overflow: hidden;
    background: var(--card-bg);
    box-shadow: 0 10px 30px rgba(0,0,0,0.12);
  }
  .card-swoosh { position: absolute; inset: 0; width: 1000px; height: 568px; }
  .brand-mark {
    position: absolute; left: 70px; top: 58px;
    width: 200px; height: 200px; border-radius: 50%;
    background: radial-gradient(circle at 50% 60%, var(--ember), var(--flame) 55%, var(--wine) 100%);
  }
  .brand-name {
    position: absolute; left: 290px; top: 150px;
    color: var(--brand-text); font-weight: 400; line-height: 1;
  }
  .brand-name .word { display: block; font-size: 72px; letter-spacing: 1px; }
  .brand-name .tagline { display: block; font-size: 22px; letter-spacing: 1.5px; margin-top: 16px; }
  .person { position: absolute; left: 290px; top: 290px; }
  .person-name { font-size: 36px; font-weight: 700; color: var(--wine); }
  .person-title { font-size: 24px; font-weight: 600; color: var(--ember); margin-top: 2px; }
  .contact {
    position: absolute; right: 46px; top: 424px;
    list-style: none; text-align: right;
  }
  .contact li {
    display: flex; justify-content: flex-end; align-items: center;
    gap: 18px; height: 38px;
    font-size: 23px; font-weight: 300; color: var(--contact-text);
  }
  .contact svg { width: 24px; height: 24px; fill: var(--ember); }
</style>
</head>
<body>
<div class="canvas">
  <div class="card">
    <svg class="card-swoosh" viewBox="0 0 1000 568" aria-hidden="true">
      <defs>
        <linearGradient id="wineFill" x1="0" y1="1" x2="1" y2="0">
          <stop offset="0" stop-color="var(--wine-dark)"/>
          <stop offset="0.6" stop-color="var(--wine)"/>
          <stop offset="1" stop-color="var(--wine-light)"/>
        </linearGradient>
      </defs>
      <path d="M60 568 C480 545 820 400 1000 10 L1000 568 Z" fill="url(#wineFill)"/>
      <path d="M60 568 C480 545 820 400 1000 10" fill="none" stroke="var(--ember)" stroke-width="3" opacity="0.7"/>
    </svg>

    <div class="brand-mark" role="img" aria-label="Brand emblem area"></div>
    <div class="brand-name">
      <span class="word">VALCORNE</span>
      <span class="tagline">HEALTH CARE MARKETING</span>
    </div>

    <div class="person">
      <div class="person-name">Marla Tenwick</div>
      <div class="person-title">CEO</div>
    </div>

    <ul class="contact">
      <li>(512)638-2974
        <svg viewBox="0 0 24 24" aria-hidden="true"><path d="M6.6 10.8a15.1 15.1 0 0 0 6.6 6.6l2.2-2.2a1 1 0 0 1 1-.25 11.4 11.4 0 0 0 3.6.57 1 1 0 0 1 1 1V20a1 1 0 0 1-1 1A17 17 0 0 1 3 4a1 1 0 0 1 1-1h3.5a1 1 0 0 1 1 1c0 1.25.2 2.45.57 3.57a1 1 0 0 1-.25 1z"/></svg>
      </li>
      <li>marla@valcorne.com
        <svg viewBox="0 0 24 24" aria-hidden="true"><path d="M2 5h20v14H2z M3 6l9 7 9-7" /><path d="M2 5h20L12 12z" fill="#fbd0b0"/></svg>
      </li>
      <li>www.valcorne.com
        <svg viewBox="0 0 24 24" aria-hidden="true"><circle cx="12" cy="12" r="10"/><path d="M2 12h20M12 2c3 3 3 17 0 20M12 2c-3 3-3 17 0 20" stroke="#fbd0b0" stroke-width="1.4" fill="none"/></svg>
      </li>
    </ul>
  </div>
</div>
</body>
</html>
```